Meadowlark Property Review is a leading provider of residential appraisal and home inspection products in S

I need a business card/logo designed that obviously describes my business. We are a residential appraisal and home inspection company in Springfield, MO. We offer residential appraisals, home inspection, pest inspection and radon gas measurement. We have been in business for 18 years and hold state certified residential appraisal licenses and OBREX certified home inspection licenses. I have a logo that I really like and will attach, but would be open to new suggestions. I like more modern designs than traditional and would like a two sided card with our services, licenses and qualifications on the back.

```html
<!DOCTYPE html>
<html lang="en">
<head>
<meta charset="utf-8">
<title>Meadowlark Property Review – Business Card</title>
<link rel="stylesheet" href="https://fonts.googleapis.com/css2?family=PT+Sans:ital,wght@0,400;0,700;1,400&display=swap">
<style>
  :root {
    --page-bg: #e9e4df;
    --card-brown-dark: #5a3a28;
    --card-brown: #7a5238;
    --card-brown-light: #9a7156;
    --frost-light: #efe9e4;
    --frost-mid: #d9cfc7;
    --accent-orange: #e2731f;
    --text-light: #f7efe8;
    --logo-ink: #4a2f20;
  }
  html, body {
    margin: 0;
    width: 1200px;
    height: 969px;
    overflow: hidden;
    background: var(--page-bg);
  }
  .canvas {
    position: relative;
    width: 1200px;
    height: 969px;
  }
  .business-card {
    position: absolute;
    left: 100px;
    top: 200px;
    width: 1000px;
    height: 570px;
    border-radius: 26px;
    overflow: hidden;
    box-shadow: 0 14px 40px rgba(60, 40, 25, 0.25);
    font-family: "PT Sans", sans-serif;
  }
  .card-art {
    position: absolute;
    inset: 0;
    width: 1000px;
    height: 570px;
  }
  .contact-block {
    position: absolute;
    left: 50px;
    top: 38px;
    color: var(--text-light);
  }
  .person-name {
    margin: 0;
    font-size: 33px;
    font-weight: 400;
    color: var(--accent-orange);
    line-height: 1.1;
  }
  .person-title {
    margin: 4px 0 0;
    font-size: 25px;
    line-height: 1.2;
  }
  .postal-address {
    margin: 28px 0 0;
    font-style: normal;
    font-size: 22px;
    line-height: 1.35;
  }
  .contact-list {
    list-style: none;
    margin: 24px 0 0;
    padding: 0;
    font-size: 22px;
  }
  .contact-list li {
    display: flex;
    align-items: center;
    gap: 16px;
    height: 38px;
  }
  .contact-icon {
    width: 20px;
    height: 20px;
    flex: none;
  }
  .service-list {
    list-style: none;
    margin: 20px 0 0;
    padding: 0;
    font-size: 23px;
    font-style: italic;
    line-height: 1.42;
  }
  .service-list li {
    position: relative;
    padding-left: 30px;
  }
  .service-list li::before {
    content: "";
    position: absolute;
    left: 2px;
    top: 14px;
    width: 7px;
    height: 7px;
    border-radius: 50%;
    background: var(--accent-orange);
  }
  .service-list .service-continued {
    color: #f0c8b8;
  }
  .brand-mark {
    position: absolute;
    left: 612px;
    top: 442px;
    display: flex;
    align-items: center;
    gap: 12px;
  }
  .brand-square {
    width: 20px;
    height: 20px;
    background: var(--accent-orange);
  }
  .brand-name {
    font-size: 26px;
    font-weight: 700;
    color: var(--logo-ink);
    white-space: nowrap;
  }
</style>
</head>
<body>
<main class="canvas">
  <section class="business-card" aria-label="Meadowlark Property Review business card">
    <svg class="card-art" viewBox="0 0 1000 570" role="img" aria-label="Background artwork: brown field blending into frosted roof-line decoration">
      <defs>
        <linearGradient id="cardGradient" x1="0" y1="0" x2="1" y2="0">
          <stop offset="0" stop-color="var(--card-brown-light)"/>
          <stop offset="0.3" stop-color="var(--card-brown)"/>
          <stop offset="0.46" stop-color="var(--card-brown-dark)"/>
          <stop offset="0.6" stop-color="var(--frost-mid)"/>
          <stop offset="1" stop-color="var(--frost-light)"/>
        </linearGradient>
      </defs>
      <rect class="card-field" width="1000" height="570" fill="url(#cardGradient)"/>
    </svg>

    <div class="contact-block">
      <h1 class="person-name">Daniel Reyes</h1>
      <p class="person-title">CEO/Founder</p>
      <address class="postal-address">2140 Cedar Hollow Road<br>Springfield, Missouri 65804</address>
      <ul class="contact-list">
        <li>
          <svg class="contact-icon" viewBox="0 0 20 20" aria-label="Phone"><path d="M5 2 L8 2 L9 6 L7 8 Q9 12 12 13 L14 11 L18 12 L18 15 Q17 18 14 18 Q3 16 2 5 Q2 2 5 2 Z" fill="var(--accent-orange)"/></svg>
          <span>417 555 0182</span>
        </li>
        <li>
          <svg class="contact-icon" viewBox="0 0 20 20" aria-label="Fax"><rect x="5" y="2" width="10" height="6" fill="var(--accent-orange)"/><rect x="1" y="8" width="18" height="8" rx="2" fill="var(--accent-orange)"/><rect x="5" y="13" width="10" height="5" fill="var(--text-light)"/></svg>
          <span>417 555 0147</span>
        </li>
        <li>
          <svg class="contact-icon" viewBox="0 0 20 20" aria-label="Email"><rect x="1" y="4" width="18" height="12" fill="var(--accent-orange)"/><path d="M1 4 L10 11 L19 4" fill="none" stroke="var(--card-brown-dark)" stroke-width="1.5"/></svg>
          <span>hello@meadowlarkreview.com</span>
        </li>
        <li>
          <svg class="contact-icon" viewBox="0 0 20 20" aria-label="Website"><circle cx="10" cy="10" r="9" fill="var(--accent-orange)"/><path d="M1 10 H19 M10 1 Q5 10 10 19 M10 1 Q15 10 10 19" fill="none" stroke="var(--card-brown-dark)" stroke-width="1.2"/></svg>
          <span>www.meadowlarkreview.com</span>
        </li>
      </ul>
      <ul class="service-list">
        <li>Residential appraisals</li>
        <li>Home inspection</li>
        <li>Pest inspection and</li>
        <li class="service-continued">radon gas measurement.</li>
      </ul>
    </div>

    <div class="brand-mark">
      <span class="brand-square" aria-hidden="true"></span>
      <span class="brand-name">Meadowlark Property Review</span>
    </div>
  </section>
</main>
</body>
</html>
```